Corvane Capital Business Cards

These are professional business cards that are for my family office.
Put fake emails and phone numbers as of now until I finalize those components. This family office controls my families investments, assets, and future. The cards should be professional.
..
.
.
.
I just uploaded another variation of a logo I would like to see as a business card to I am inbeteen which logo to use

Target Market(s)

business

Industry/Entity Type

business

Contact Information for Business Card

Professional, wealth related, finance related.

Requirements
Must have
• Logo

```html
<!DOCTYPE html>
<html lang="en">
<head>
<meta charset="utf-8">
<title>Corvane Capital Business Cards</title>
<link href="https://fonts.googleapis.com/css2?family=Playfair+Display:wght@400;700&family=Arimo:wght@400&display=swap" rel="stylesheet">
<style>
  :root {
    --backdrop: #1a1a1a;
    --card: #262626;
    --gold: #c2a868;
    --white: #ffffff;
    --text: #f2f2f2;
  }
  * { box-sizing: border-box; margin: 0; padding: 0; }
  html, body { width: 1200px; height: 900px; overflow: hidden; }
  body { background: var(--backdrop); position: relative; font-family: "Arimo", Arial, sans-serif; }

  .card {
    position: absolute;
    width: 700px;
    height: 400px;
    background: var(--card);
    border-radius: 22px;
    overflow: hidden;
    box-shadow: 0 12px 30px rgba(0,0,0,0.6);
  }
  .card--front { left: 110px; top: 45px; }
  .card--back { left: 390px; top: 470px; }

  .wordmark {
    font-family: "Playfair Display", Georgia, serif;
    font-weight: 400;
    color: var(--gold);
    letter-spacing: 0.08em;
    text-transform: uppercase;
    white-space: nowrap;
    display: flex;
    align-items: center;
    gap: 14px;
  }
  .wordmark__square { width: 14px; height: 14px; background: var(--gold); flex: none; }

  .card--front .wordmark {
    position: absolute; left: 0; right: 0; top: 0; bottom: 0;
    justify-content: center; font-size: 46px;
  }

  .card--back .wordmark {
    position: absolute; left: 34px; top: 176px; font-size: 28px;
  }
  .divider {
    position: absolute; left: 362px; top: 78px; width: 1.5px; height: 210px; background: var(--gold);
  }
  .contact { position: absolute; left: 392px; top: 70px; color: var(--text); }
  .contact__name {
    font-family: "Playfair Display", Georgia, serif; font-weight: 700;
    color: var(--gold); font-size: 24px; letter-spacing: 0.03em; text-transform: uppercase; line-height: 1.1;
  }
  .contact__role { font-size: 15px; margin-top: 4px; }
  .contact__address { font-size: 15px; line-height: 1.3; margin-top: 14px; }
  .contact__list { list-style: none; margin-top: 12px; font-size: 15px; line-height: 1.6; }
  .contact__list li { display: flex; align-items: center; gap: 8px; }
  .contact__list svg { width: 13px; height: 13px; flex: none; }

  .edge-band { position: absolute; left: 0; bottom: 0; width: 700px; height: 30px; }
</style>
</head>
<body>
  <section class="card card--front" aria-label="Card front">
    <div class="wordmark"><span class="wordmark__square"></span>Corvane Capital</div>
  </section>

  <section class="card card--back" aria-label="Card back">
    <div class="wordmark"><span class="wordmark__square"></span>Corvane Capital</div>
    <div class="divider"></div>
    <div class="contact">
      <p class="contact__name">Elliot Marsh</p>
      <p class="contact__role">CEO/Founder</p>
      <p class="contact__address">4820 Linden Park Rd Suite 200<br>Ashford, AB 562108</p>
      <ul class="contact__list">
        <li>
          <svg viewBox="0 0 16 16" aria-hidden="true"><path fill="var(--gold)" d="M3 2h3l1.5 3.5-2 1.3a9 9 0 0 0 3.7 3.7l1.3-2L14 10v3a1 1 0 0 1-1 1A11 11 0 0 1 2 3a1 1 0 0 1 1-1z"/></svg>
          (555) 014-2273
        </li>
        <li>
          <svg viewBox="0 0 16 16" aria-hidden="true"><rect x="1" y="3.5" width="14" height="9" fill="var(--gold)"/><path d="M1.5 4l6.5 5 6.5-5" fill="none" stroke="var(--card)" stroke-width="1.2"/></svg>
          ElliotM@corvanecapital.com
        </li>
        <li>
          <svg viewBox="0 0 16 16" aria-hidden="true"><circle cx="8" cy="8" r="6.5" fill="none" stroke="var(--gold)" stroke-width="1.5"/><path d="M1.5 8h13M8 1.5c-3 3.5-3 9.5 0 13M8 1.5c3 3.5 3 9.5 0 13" fill="none" stroke="var(--gold)" stroke-width="1.2"/></svg>
          www.corvanecapital.com
        </li>
      </ul>
    </div>
    <svg class="edge-band" viewBox="0 0 700 30" preserveAspectRatio="none" aria-hidden="true">
      <polygon points="0,22 372,22 362,30 0,30" fill="var(--white)"/>
      <polygon points="378,12 700,12 700,30 366,30" fill="var(--gold)"/>
    </svg>
  </section>
</body>
</html>
```